Kelvaro.ch is looking for business card letterhead and envelope C5 with WOW effect

We need a strong business card for our company Kelvaro.ch, logo is available. You want a black or dark background on which the logo Stark r% 26 # 252; appears. Letterhead and envelope in C5 format should be in a similar design, but does not have to be We need a strong business card for our company Kelvaro.ch, logo is available. A black or dark background is desired, on which the logo Stark comes across. The letterhead and the envelope in C5 format should have a similar design.

Target Market(s)

Private customers as well as entrepreneurs

Contact Information for Business Card

E-mail: info@kelvaro-example.ch
Web.www.Kelvaro-example.ch
Tel: +41 ( 0 ) 79 482 6037
Adresse:
Lindenweg 14
9406 Tarnbach

Hier kann man Icons verwenden für Email,Tel und Adressse

Font styles to use
Other font styles liked:
• Dubai,bold

Colors

Designer to choose colors to be used in the design.

Requirements
Must have
• WOW effect
Nice to have
• R% 26 # 252; back business card with our service listings. - VEHICLE LABELING - SHOP WINDOW LABELING - STICKERS AND MUCH MORE ... in red color

```html
<!DOCTYPE html>
<html lang="en">
<head>
<meta charset="utf-8">
<title>Kelvaro.ch – Business Card</title>
<link rel="stylesheet" href="https://fonts.googleapis.com/css2?family=Roboto:wght@300;400;500;700&display=swap">
<style>
  :root {
    --backdrop: #3a3a3a;
    --card: #1d1d1d;
    --ink: #f2f2f2;
    --muted: #cfcfcf;
    --yellow: #f7c915;
    --red: #d8262b;
    --rule: #8a8a8a;
  }
  * { box-sizing: border-box; margin: 0; padding: 0; }
  html, body {
    width: 1200px; height: 880px; overflow: hidden;
    background: var(--backdrop);
    font-family: "Roboto", Arial, sans-serif;
    color: var(--ink);
  }
  .canvas {
    position: relative; width: 1200px; height: 880px;
  }
  .card {
    position: absolute; left: 290px;
    width: 620px; height: 354px;
    background: var(--card);
    border-radius: 18px;
    box-shadow: 0 14px 30px rgba(0,0,0,.45);
  }
  .card--services { top: 66px; }
  .card--contact { top: 460px; }

  .brand {
    display: flex; align-items: center; gap: 12px;
    font-weight: 700; color: var(--ink);
    letter-spacing: 1px; text-transform: uppercase;
  }
  .brand__dot {
    width: 26px; height: 26px; border-radius: 50%;
    background: var(--yellow);
  }

  /* services side */
  .card--services .brand {
    position: absolute; left: 180px; top: 92px; font-size: 38px;
  }
  .card--services .brand__dot { width: 34px; height: 34px; }
  .services {
    position: absolute; left: 0; right: 0; top: 182px; text-align: center;
  }
  .services__title {
    color: var(--yellow); font-size: 30px; font-weight: 500; margin-bottom: 12px;
  }
  .services__list {
    list-style: none; color: var(--red);
    font-size: 17px; text-transform: uppercase; line-height: 1.6;
  }
  .services__list li { display: inline; }
  .services__list li::before {
    content: ""; display: inline-block; width: 8px; height: 8px;
    border-radius: 50%; background: var(--yellow);
    margin: 0 8px 2px 14px; vertical-align: middle;
  }
  .services__list .break { display: block; height: 0; }

  /* contact side */
  .card--contact .brand {
    position: absolute; left: 58px; top: 176px; font-size: 30px;
  }
  .divider {
    position: absolute; left: 352px; top: 70px; width: 1px; height: 214px;
    background: var(--rule);
  }
  .person {
    position: absolute; left: 384px; top: 70px;
  }
  .person__name { color: var(--yellow); font-size: 27px; font-weight: 500; }
  .person__role { color: var(--muted); font-size: 15px; font-weight: 300; margin-top: 2px; }
  .contacts {
    position: absolute; left: 384px; top: 150px;
    list-style: none; font-size: 16px; font-weight: 300; color: var(--ink);
  }
  .contacts li { display: flex; align-items: flex-start; gap: 10px; line-height: 1.3; }
  .contacts li + li { margin-top: 6px; }
  .contacts .address { margin-bottom: 8px; }
  .contacts svg { flex: 0 0 16px; width: 16px; height: 16px; margin-top: 2px; fill: var(--yellow); }
  .hl { color: var(--yellow); }
</style>
</head>
<body>
<main class="canvas">

  <section class="card card--services">
    <div class="brand"><span class="brand__dot"></span><span>Kelvaro.ch</span></div>
    <div class="services">
      <h2 class="services__title">our service listings</h2>
      <ul class="services__list">
        <li>Vehicle labeling</li><li>Shop window labeling</li><span class="break"></span><li>Stickers and much more</li>
      </ul>
    </div>
  </section>

  <section class="card card--contact">
    <div class="brand"><span class="brand__dot"></span><span>Kelvaro.ch</span></div>
    <div class="divider"></div>
    <div class="person">
      <h1 class="person__name">Lukas Brenner</h1>
      <p class="person__role">Manager</p>
    </div>
    <ul class="contacts">
      <li class="address">
        <svg viewBox="0 0 16 16" aria-hidden="true"><path d="M8 1a5 5 0 0 0-5 5c0 3.6 5 9 5 9s5-5.4 5-9a5 5 0 0 0-5-5zm0 7a2 2 0 1 1 0-4 2 2 0 0 1 0 4z"/></svg>
        <span>Lindenweg 14<br>9406 Tarnbach</span>
      </li>
      <li>
        <svg viewBox="0 0 16 16" aria-hidden="true"><path d="M3.6 1.5l2.2 2.6-1.2 1.7a9 9 0 0 0 5.6 5.6l1.7-1.2 2.6 2.2-1.4 2.1C7.6 14.2 1.8 8.4 1.5 2.9z"/></svg>
        <span>+41 ( 0 ) 79 482 6037</span>
      </li>
      <li>
        <svg viewBox="0 0 16 16" aria-hidden="true"><path d="M1 4h14v9H1zM1.8 4.6L8 9.2l6.2-4.6" stroke="#1d1d1d" stroke-width="1.2"/></svg>
        <span>info@kelvaro-example.ch</span>
      </li>
      <li>
        <svg viewBox="0 0 16 16" aria-hidden="true"><path d="M8 1a7 7 0 1 0 0 14A7 7 0 0 0 8 1zm0 2.2a4.8 4.8 0 1 1 0 9.6 4.8 4.8 0 0 1 0-9.6zM8 5.5a2.5 2.5 0 1 0 0 5 2.5 2.5 0 0 0 0-5z"/></svg>
        <span>www.<span class="hl">Kelvaro-example</span>.ch</span>
      </li>
    </ul>
  </section>

</main>
</body>
</html>
```